Beautiful design for wordpress

I need a beautiful, colourful and feminine website. My business is called 'The Velvet Lantern', and I sell crystals, books, CD's, pendulums and other metaphysical items. I also provide Reiki (energy healing).
I want this design to be eye catching and inspire happiness and joy in those who see it. And I would love to see the use of the logo and its colours :)
Please add these on the web design: Home, About, Online store, Blog

Industry/Entity Type

Business

Requirements
Must have
• Colourful and playful, must use the logo somewhere, have the words on a menu saying 'Home, Blog, Online store and about' (or similar to those)And the design must stand out!
Should not have
• grey, brown and other boring colours.

```html
<!DOCTYPE html>
<html lang="en">
<head>
<meta charset="utf-8">
<title>The Velvet Lantern — Crystals &amp; Gifts</title>
<link href="https://fonts.googleapis.com/css2?family=Noto+Serif:wght@400;700&family=Open+Sans:wght@400;600&display=swap" rel="stylesheet">
<style>
  :root{
    --orange:#ffa84a;
    --orange-deep:#f7931e;
    --magenta:#e62fa3;
    --magenta-deep:#d41d8f;
    --page:#f7f7f7;
    --ink:#222;
    --muted:#555;
    --icon:#5a5a5a;
    --white:#fff;
  }
  *{box-sizing:border-box;margin:0;padding:0}
  html,body{width:892px;height:1200px;overflow:hidden}
  body{position:relative;background:var(--white);font-family:"Noto Serif",Georgia,serif;color:var(--ink)}
  .top-band{position:absolute;left:0;top:0;width:892px;height:454px;background:var(--orange)}
  .page{position:absolute;left:61px;top:41px;width:774px;height:1077px;background:var(--page);border-radius:3px;box-shadow:0 0 3px rgba(0,0,0,.08)}
  .abs{position:absolute}

  .brand{left:17px;top:70px;width:200px;display:flex;align-items:center;gap:10px;font-size:26px;line-height:1.15;color:var(--magenta)}
  .brand-dot{flex:none;width:18px;height:18px;border-radius:50%;background:var(--orange)}
  .brand-sub{left:56px;top:186px;font-size:9px;letter-spacing:2px;color:var(--muted);white-space:nowrap}

  .cart{right:21px;top:25px;font-size:11px;color:var(--muted);display:flex;align-items:center;gap:10px;white-space:nowrap}
  .social{right:21px;top:62px;display:flex;gap:1px}
  .social span{width:28px;height:28px;border-radius:50%;background:var(--icon);display:flex;align-items:center;justify-content:center}
  .tollfree{right:21px;top:113px;font-size:12.5px;white-space:nowrap}
  .tollfree b{font-weight:700}

  .nav{left:289px;top:156px;width:464px;height:38px;background:linear-gradient(var(--magenta),var(--magenta-deep));display:flex}
  .nav a{color:var(--white);text-decoration:none;font-size:12.5px;line-height:38px;text-align:center;white-space:nowrap;flex:none}
  .nav a.active{background:linear-gradient(#ffab52,var(--orange-deep))}
  .nav .w-home{width:68px}.nav .w-about{width:116px}.nav .w-store{width:106px}.nav .w-blog{width:68px}.nav .w-contact{width:106px}

  .hero{left:17px;top:208px;width:736px;height:311px;
    background:
      radial-gradient(ellipse 150px 190px at 60% 62%, rgba(236,146,60,.85), rgba(236,146,60,0) 100%),
      radial-gradient(ellipse 90px 110px at 58% 30%, rgba(120,90,80,.6), rgba(120,90,80,0) 100%),
      linear-gradient(180deg,#c7cacf 0%,#b3b9c4 38%,#3f60b0 52%,#7f93c2 66%,#c9ccd4 85%,#b4bac5 100%)}
  .hero-caption{left:17px;top:333px;width:293px;height:60px;background:rgba(20,24,36,.88);color:var(--white);font-size:18px;line-height:60px;padding-left:25px;white-space:nowrap}
  .dots{left:351px;top:508px;width:68px;height:22px;border-radius:4px;background:linear-gradient(#fafafa,#ddd);border:1px solid #ccc;display:flex;justify-content:center;align-items:center;gap:9px}
  .dots span{width:9px;height:9px;border-radius:50%;border:1px solid #888;background:#eee}

  .tile{top:578px;width:179px;height:223px;background:var(--white);border:1px solid #e3e3e3;padding:6px}
  .tile-photo{position:relative;width:100%;height:100%}
  .tile-label{position:absolute;left:0;bottom:0;width:100%;height:42px;background:rgba(0,0,0,.72);color:var(--white);font-family:"Open Sans",Arial,sans-serif;font-size:14.5px;font-weight:600;line-height:42px;padding-left:13px}
  .p-crystals{background:radial-gradient(ellipse 60px 50px at 45% 45%,rgba(90,150,190,.7),rgba(90,150,190,0)),radial-gradient(ellipse 50px 40px at 80% 60%,rgba(190,190,200,.6),rgba(190,190,200,0)),linear-gradient(#1e1e22,#4a4f5a 50%,#141418)}
  .p-books{background:radial-gradient(ellipse 50px 70px at 30% 35%,rgba(220,60,80,.6),rgba(220,60,80,0)),radial-gradient(ellipse 60px 60px at 70% 70%,rgba(240,200,60,.5),rgba(240,200,60,0)),linear-gradient(#e2ddd4,#8c6c8e 45%,#4a6aa5 80%,#6b4a3e)}
  .p-cds{background:radial-gradient(ellipse 50px 40px at 80% 20%,rgba(240,220,40,.7),rgba(240,220,40,0)),radial-gradient(ellipse 60px 50px at 20% 80%,rgba(200,70,60,.5),rgba(200,70,60,0)),linear-gradient(#d8c08a,#3c3c40 40%,#5a4a44 100%)}
  .p-others{background:radial-gradient(ellipse 70px 50px at 45% 82%,rgba(190,150,120,.8),rgba(190,150,120,0)),linear-gradient(#8fb8e2,#c6dbef 55%,#e6e6e6 75%,#6e5446)}

  .welcome-title{left:17px;top:844px;font-size:19px;color:var(--magenta);font-weight:400;white-space:nowrap}
  .welcome-photo{left:17px;top:879px;width:178px;height:94px;background:radial-gradient(ellipse 50px 45px at 55% 55%,rgba(230,210,170,.9),rgba(230,210,170,0)),linear-gradient(90deg,#8aa0c4,#c9b8a4 50%,#9fb0c9)}
  .welcome-text{left:203px;top:877px;width:305px;font-size:11px;line-height:23.3px;color:#444}
  .btn{left:17px;top:985px;width:66px;height:40px;background:linear-gradient(var(--magenta),var(--magenta-deep));color:var(--white);font-size:10.5px;line-height:40px;text-align:center;white-space:nowrap}

  .store{left:513px;top:848px;width:240px;height:185px;border:1px solid #ddd;background:linear-gradient(#f8f8f8,#e4e4e4);padding:18px 13px}
  .store h2{font-size:16px;font-weight:400;color:var(--magenta);margin-bottom:16px}
  .store p{font-size:11px;line-height:19px;color:#444;margin-bottom:9px}
  .store .addr{width:200px}

  .footer-nav{position:absolute;top:1141px;left:0;width:892px;display:flex;justify-content:center;gap:36px;font-size:10.5px}
  .copyright{position:absolute;top:1163px;left:0;width:892px;text-align:center;font-size:10.5px}
</style>
</head>
<body>
  <div class="top-band"></div>
  <main class="page">
    <div class="abs brand"><span class="brand-dot"></span><span>The Velvet Lantern</span></div>
    <div class="abs brand-sub">CRYSTALS &amp; GIFTS</div>

    <div class="abs cart">
      <span>Your Shopping cart</span>
      <svg width="14" height="12" viewBox="0 0 14 12" aria-hidden="true"><path d="M1 4h12l-2 7H3z M4 4l3-3 3 3" fill="none" stroke="#555" stroke-width="1.3"/></svg>
      <span>0items</span>
    </div>
    <div class="abs social" aria-label="Social links">
      <span><svg width="14" height="14" viewBox="0 0 14 14" aria-label="Share"><circle cx="3" cy="7" r="2" fill="#fff"/><circle cx="11" cy="3" r="2" fill="#fff"/><circle cx="11" cy="11" r="2" fill="#fff"/><path d="M3 7L11 3M3 7l8 4" stroke="#fff" stroke-width="1.3"/></svg></span>
      <span><svg width="14" height="14" viewBox="0 0 14 14" aria-label="Email"><rect x="1" y="3" width="12" height="8" rx="1" fill="none" stroke="#fff" stroke-width="1.4"/><path d="M1.5 3.5L7 8l5.5-4.5" fill="none" stroke="#fff" stroke-width="1.4"/></svg></span>
      <span><svg width="14" height="14" viewBox="0 0 14 14" aria-label="Website"><circle cx="7" cy="7" r="5.5" fill="none" stroke="#fff" stroke-width="1.3"/><ellipse cx="7" cy="7" rx="2.3" ry="5.5" fill="none" stroke="#fff" stroke-width="1.1"/><path d="M1.5 7h11" stroke="#fff" stroke-width="1.1"/></svg></span>
      <span><svg width="14" height="14" viewBox="0 0 14 14" aria-label="Chat"><path d="M2 2.5h10a1 1 0 0 1 1 1v5a1 1 0 0 1-1 1H6l-3 2.5V9.5H2a1 1 0 0 1-1-1v-5a1 1 0 0 1 1-1z" fill="#fff"/></svg></span>
    </div>
    <div class="abs tollfree">Toll Free number: <b>1800 555 0199</b></div>

    <nav class="abs nav">
      <a class="active w-home" href="#">Home</a><a class="w-about" href="#">About Us</a><a class="w-store" href="#">Online store</a><a class="w-blog" href="#">Blog</a><a class="w-contact" href="#">Contact us</a>
    </nav>

    <div class="abs hero" role="img" aria-label="Young woman with headphones browsing CDs in a music store"></div>
    <div class="abs hero-caption">Store to Buy Music CD Online</div>
    <div class="abs dots"><span></span><span></span><span></span></div>

    <div class="abs tile" style="left:15px"><div class="tile-photo p-crystals" role="img" aria-label="Crystal rings and jewellery on display"><span class="tile-label">Crystals</span></div></div>
    <div class="abs tile" style="left:202px"><div class="tile-photo p-books" role="img" aria-label="Bookshelves full of colourful books"><span class="tile-label">Books</span></div></div>
    <div class="abs tile" style="left:388px"><div class="tile-photo p-cds" role="img" aria-label="Racks of music CDs"><span class="tile-label">CD's</span></div></div>
    <div class="abs tile" style="left:574px"><div class="tile-photo p-others" role="img" aria-label="Reiki energy healing session"><span class="tile-label">Others</span></div></div>

    <h1 class="abs welcome-title">Welcome to The Velvet Lantern</h1>
    <div class="abs welcome-photo" role="img" aria-label="Woman with headphones browsing music"></div>
    <p class="abs welcome-text">Lorem ipsum dolor sit amet, consectetur adipisicing elit, sed do eiusmod tempor incididunt ut labore et dolore magna aliqua. Ut enim ad minim veniam, quis nostrud exercitation ullamco laboris nisi ut aliquip ex ea commodo consequat.</p>
    <div class="abs btn">Read More</div>

    <aside class="abs store">
      <h2>Store Information</h2>
      <p class="addr">17 rue des Glycines 75011 Paris France</p>
      <p>Call us now: 0142-555-018</p>
      <p>Email: hello@velvetlantern.example</p>
    </aside>
  </main>

  <nav class="footer-nav"><span>Home</span><span>About Us</span><span>Online store</span><span>Blog</span><span>Contact us</span></nav>
  <p class="copyright">Copyright © 2014 The Velvet Lantern. All rights reserved.</p>
</body>
</html>
```